Korvile

I'd like new business card design options. I'll need to provide updated contact info although after the deign is complete. We are in IT, specifically in the data backup, archiving and disaster recovery verticals.

Industry/Entity Type

Business

```html
<!DOCTYPE html>
<html lang="en">
<head>
<meta charset="utf-8">
<title>Korvile Business Card</title>
<link rel="stylesheet" href="https://fonts.googleapis.com/css2?family=Montserrat:wght@600;700&family=Lato:wght@400;700&display=swap">
<style>
  :root {
    --backdrop: #3b3b3b;
    --card-white: #ffffff;
    --brand-blue: #1658b4;
    --name-blue: #1a4fa8;
    --ink: #1e1e1e;
    --rule-blue: #2a6ccc;
    --back-deep: #0a56b0;
    --back-bright: #0b8fd9;
    --back-text: #ffffff;
  }
  * { margin: 0; padding: 0; box-sizing: border-box; }
  html, body {
    width: 1200px; height: 900px; overflow: hidden;
    background: var(--backdrop);
  }
  .canvas { position: relative; width: 1200px; height: 900px; }

  .card {
    position: absolute; top: 170px;
    width: 347px; height: 561px;
  }
  .card--front { left: 259px; background: var(--card-white); }
  .card--back {
    left: 631px;
    background: radial-gradient(ellipse at 70% 35%, var(--back-bright) 0%, #0678cb 55%, var(--back-deep) 100%);
  }

  .wordmark {
    position: absolute; left: 0; right: 0;
    display: flex; align-items: center; justify-content: center; gap: 12px;
    font-family: "Montserrat", sans-serif; font-weight: 700;
    font-size: 30px; letter-spacing: 4px; text-transform: uppercase;
  }
  .wordmark__dot { width: 34px; height: 34px; border-radius: 50%; }
  .card--front .wordmark { top: 308px; top: 138px; color: var(--brand-blue); }
  .card--front .wordmark__dot { background: var(--brand-blue); }
  .card--back .wordmark { top: 210px; color: var(--back-text); }
  .card--back .wordmark__dot { background: var(--back-text); }

  .contact {
    position: absolute; left: 0; right: 0; top: 334px;
    text-align: center; font-family: "Lato", sans-serif; color: var(--ink);
  }
  .contact__name {
    font-family: "Montserrat", sans-serif; font-weight: 600;
    font-size: 20px; color: var(--name-blue); letter-spacing: 0.2px; line-height: 26px;
  }
  .contact__role { font-size: 15px; line-height: 20px; }
  .contact__divider {
    display: flex; align-items: center; justify-content: center; gap: 6px;
    margin: 12px 0 6px;
  }
  .contact__rule { width: 34px; height: 1px; background: var(--rule-blue); }
  .contact__divider svg { width: 13px; height: 11px; fill: var(--name-blue); }
  .contact__line { font-size: 15px; line-height: 20.5px; }
  .contact__address { margin-top: 9px; }

  .services {
    position: absolute; left: 0; right: 0; top: 390px;
    text-align: center; color: var(--back-text);
    font-family: "Lato", sans-serif; font-weight: 700; font-size: 16px; line-height: 25px;
  }
  .back-rule {
    position: absolute; left: 44px; right: 44px; top: 477px;
    height: 1px; background: rgba(255,255,255,0.75);
  }
  .website {
    position: absolute; left: 0; right: 0; top: 495px;
    text-align: center; color: var(--back-text);
    font-family: "Lato", sans-serif; font-size: 18px; letter-spacing: 2.4px;
  }
</style>
</head>
<body>
<main class="canvas">
  <section class="card card--front">
    <div class="wordmark"><span class="wordmark__dot"></span>Korvile</div>
    <div class="contact">
      <p class="contact__name">DANIEL HARTLEY</p>
      <p class="contact__role">Managing Director</p>
      <div class="contact__divider">
        <span class="contact__rule"></span>
        <svg viewBox="0 0 13 11" aria-hidden="true"><path d="M1 4c2-3 9-3 11 0l-1 2-2-1V3.5C7.5 3 5.5 3 4 3.5V5L2 6zM3 7h7l1 4H2z"/></svg>
        <svg viewBox="0 0 13 11" aria-hidden="true"><path d="M3 0h6v3H3zM1 3.5h11v5H10V11H3V8.5H1zM4 7v3h5V7z"/></svg>
        <svg viewBox="0 0 13 11" aria-hidden="true"><path d="M0 1h13v9H0zM1 2l5.5 4L12 2z"/></svg>
        <span class="contact__rule"></span>
      </div>
      <p class="contact__line">(044)123456789</p>
      <p class="contact__line">(044)123456789</p>
      <p class="contact__line">info@youremail.com</p>
      <p class="contact__line contact__address">1234, Address GoesHere,</p>
      <p class="contact__line">Country name, 12345</p>
    </div>
  </section>

  <section class="card card--back">
    <div class="wordmark"><span class="wordmark__dot"></span>Korvile</div>
    <div class="services">
      <p>Data Backup</p>
      <p>Archiving</p>
      <p>Disaster Recovery Verticals</p>
    </div>
    <div class="back-rule"></div>
    <p class="website">www.websitename.com</p>
  </section>
</main>
</body>
</html>
```